PlayTallyCollective - Game Statistics and Achievement Tracking

I need a new modern design for an existing website.

The website is a project to track statistics and achievements for games (currently Vaporn Achievements/Stats and stats for Cargo Haul Odyssey 2 and Frontier Rig Journeys).
I am currently expanding the site with other platforms (like QVR) and more games.
I am also adding a user registration/signin with user profiles to show off their achievements and stats across all platforms and games.

The current website is available at https://plytly.example/
To search for data you can use the username "pixelornin" (without quotes).

The design should be modern and extendable and contain space for a logo.

The logo should match the project. It should combine Gaming with statistics.

Target Market(s)

Video game players

Number of Pages Required

5+ page

Font styles to use
Sans Serif

Requirements
Must have
• Basic Layout, User profile page (not yet available on live site), Search Page for Platforms/Games, Platform profile page, Dark theme

```html
<!DOCTYPE html>
<html lang="en">
<head>
<meta charset="utf-8">
<title>PlayTallyCollective</title>
<link rel="stylesheet" href="https://fonts.googleapis.com/css2?family=Silkscreen:wght@400;700&family=Montserrat:wght@500;600;700;800&display=swap">
<style>
  :root{
    --bg:#000;
    --ink:#fff;
    --magenta:#f01cf0;
    --violet:#6a3cf5;
    --deep:#2a0530;
    --muted:#d9d2e6;
  }
  *{margin:0;padding:0;box-sizing:border-box}
  html,body{width:1200px;height:2551px;overflow:hidden;background:var(--bg)}
  body{position:relative;font-family:"Montserrat",sans-serif;color:var(--ink)}
  .glow{position:absolute;border-radius:50%;pointer-events:none;filter:blur(20px)}
  .pixel{font-family:"Silkscreen",sans-serif;font-weight:700;letter-spacing:.18em;white-space:nowrap}
  .abs{position:absolute}
  .center{left:0;width:1200px;text-align:center}

  .brand{display:flex;align-items:center;gap:12px}
  .brand-mark{width:18px;height:18px;background:var(--magenta);flex:none}
  .brand-name{font-family:"Silkscreen",sans-serif;font-weight:700;color:var(--ink);letter-spacing:.14em;line-height:1.35;white-space:nowrap}

  .nav{display:flex;gap:41px;font-size:15px;font-weight:500;text-transform:uppercase}
  .nav a{color:var(--ink);text-decoration:none}
  .nav a.active{color:var(--magenta);text-decoration:underline;text-underline-offset:4px}

  .btn{position:absolute;display:flex;align-items:center;justify-content:center;font-weight:700;color:#fff;text-transform:uppercase;text-decoration:none;
    background:linear-gradient(90deg,var(--violet),var(--magenta));
    clip-path:polygon(0 0,88% 0,100% 22%,100% 100%,12% 100%,0 78%)}

  .stat-row{position:absolute;left:517px;font-size:15px;font-weight:700;text-transform:uppercase}
  .stat-row span{position:absolute;left:199px;white-space:nowrap;text-transform:none}

  .heading{font-family:"Silkscreen",sans-serif;font-weight:700;font-size:48px;letter-spacing:.2em;white-space:nowrap}
  .metric{position:absolute;text-align:center;width:340px}
  .metric-num{font-weight:800;font-size:52px;line-height:1}
  .metric-label{font-family:"Silkscreen",sans-serif;font-weight:700;font-size:22px;letter-spacing:.2em;margin-top:16px;line-height:1.6}
  .divider{position:absolute;width:2px;background:var(--magenta)}
  .divider::after{content:"";position:absolute;left:-9px;top:50%;width:20px;height:20px;border-radius:50%;background:var(--magenta);transform:translateY(-50%)}

  .user-card{position:absolute;top:1738px;width:273px;height:369px}
  .user-photo{position:absolute;left:10px;top:14px;width:249px;height:285px}
  .user-name{position:absolute;left:0;width:100%;top:324px;text-align:center;font-weight:600;font-size:17px}

  .footer-nav{display:flex;justify-content:center;gap:64px;font-size:24px;font-weight:600}
</style>
</head>
<body>
  <div class="glow" style="left:-150px;top:300px;width:500px;height:500px;background:radial-gradient(circle,rgba(70,40,170,.75),transparent 70%)"></div>
  <div class="glow" style="left:950px;top:-150px;width:450px;height:450px;background:radial-gradient(circle,rgba(160,20,160,.6),transparent 70%)"></div>
  <div class="glow" style="left:850px;top:850px;width:550px;height:550px;background:radial-gradient(circle,rgba(150,10,140,.7),transparent 70%)"></div>
  <div class="glow" style="left:-200px;top:1000px;width:550px;height:550px;background:radial-gradient(circle,rgba(60,30,150,.6),transparent 70%)"></div>
  <div class="glow" style="left:900px;top:1500px;width:500px;height:500px;background:radial-gradient(circle,rgba(140,10,130,.5),transparent 70%)"></div>
  <div class="glow" style="left:-150px;top:2200px;width:500px;height:500px;background:radial-gradient(circle,rgba(60,30,150,.55),transparent 70%)"></div>
  <div class="glow" style="left:950px;top:2250px;width:450px;height:450px;background:radial-gradient(circle,rgba(150,10,140,.55),transparent 70%)"></div>

  <header>
    <div class="brand abs" style="left:88px;top:38px">
      <div class="brand-mark" style="width:26px;height:26px"></div>
      <div class="brand-name" style="font-size:22px">PlayTally<br>Collective</div>
    </div>
    <nav class="nav abs" style="left:544px;top:55px">
      <a class="active" href="#">Home</a><a href="#">About Us</a><a href="#">Vaporn</a><a href="#">Game</a>
    </nav>
    <a class="btn" style="left:948px;top:40px;width:177px;height:52px;font-size:16px">Contact Us</a>
  </header>

  <section class="hero">
    <div class="abs center pixel" style="top:202px;font-size:36px;color:var(--magenta)">Welcome to</div>
    <h1 class="abs center pixel" style="top:268px;font-size:42px">PlayTally Collective</h1>
    <p class="abs center" style="top:352px;font-size:17px;font-weight:600;line-height:35px">Lorem ipsum dolor sit amet, consectetur adipiscing elit, sed do eiusmod<br>tempor incididunt ut labore et dolore magna aliqua.</p>
    <a class="btn" style="left:517px;top:457px;width:178px;height:52px;font-size:16px">Get Started</a>
  </section>

  <section class="profile">
    <svg class="abs" style="left:0;top:0" width="1200" height="1100">
      <defs>
        <linearGradient id="cardFill" x1="0" y1="0" x2="1" y2="1">
          <stop offset="0" stop-color="#16041e"/><stop offset="1" stop-color="#3a0640"/>
        </linearGradient>
        <linearGradient id="cardStroke" x1="0" y1="1" x2="1" y2="0">
          <stop offset="0" stop-color="#6a3cf5"/><stop offset="1" stop-color="#f01cf0"/>
        </linearGradient>
      </defs>
      <polygon points="111,644 967,644 1100,815 1100,1055 240,1055 111,883" fill="url(#cardFill)" stroke="url(#cardStroke)" stroke-width="2.5"/>
    </svg>
    <div class="abs" role="img" aria-label="Cartoon avatar of the player pixelornin" style="left:195px;top:708px;width:265px;height:272px;background:radial-gradient(circle at 50% 45%,#9fd8ff,#2a7fe0 60%,#0b2f7a);box-shadow:0 0 18px #1e8bff"></div>
    <div class="stat-row" style="top:718px">Played games:<span>1166/1644 (70%)</span></div>
    <div class="stat-row" style="top:764px">Total play time:<span>1 year 2 months 11 hours 25 minutes</span></div>
    <div class="stat-row" style="top:810px">Achievements:<span>18007/63070 (28%)</span></div>
    <div class="stat-row" style="top:856px">Member since:<span>14.01.2009</span></div>
    <div class="stat-row" style="top:902px">Last played:<span>Rail Route Odyssey® 5</span></div>
    <div class="stat-row" style="top:948px">Last update:<span>26.12.2024 16:00h</span></div>
    <svg class="abs" style="left:926px;top:1005px" width="140" height="24" fill="none" stroke="#fff" stroke-width="1.8" stroke-linecap="round">
      <path d="M18 12a8 8 0 1 1-3-6.2"/><path d="M15 2v4h4"/>
      <rect x="41" y="4" width="16" height="16" rx="2"/><path d="M41 9h16M45 2v4M53 2v4"/>
      <circle cx="88" cy="12" r="9" fill="#2ea0e8" stroke="none"/>
      <ellipse cx="126" cy="6" rx="9" ry="3.5"/><path d="M117 6v12c0 2 4 3.5 9 3.5s9-1.5 9-3.5V6M117 12c0 2 4 3.5 9 3.5s9-1.5 9-3.5"/>
    </svg>
  </section>

  <section class="stats">
    <h2 class="abs center heading" style="top:1140px">Our Statistics</h2>
    <svg class="abs" style="left:214px;top:1296px" width="86" height="64"><path d="M20 2h46c12 0 20 12 20 30s-4 30-14 30c-8 0-12-14-18-14H32c-6 0-10 14-18 14C4 62 0 50 0 32S8 2 20 2z" fill="var(--magenta)"/><path d="M16 24h16M24 16v16" stroke="#000" stroke-width="5"/><circle cx="62" cy="20" r="4" fill="#000"/><circle cx="70" cy="30" r="4" fill="#000"/></svg>
    <svg class="abs" style="left:572px;top:1275px" width="72" height="70" fill="var(--magenta)"><path d="M14 0h44v24c0 14-10 24-22 24S14 38 14 24z"/><path d="M14 6H2v8c0 10 8 16 14 16M58 6h12v8c0 10-8 16-14 16" fill="none" stroke="var(--magenta)" stroke-width="6"/><rect x="30" y="46" width="12" height="10"/><rect x="20" y="56" width="32" height="12" rx="3"/></svg>
    <svg class="abs" style="left:918px;top:1276px" width="82" height="84" fill="var(--magenta)"><rect x="4" y="50" width="12" height="30"/><rect x="24" y="38" width="12" height="42"/><rect x="44" y="44" width="12" height="36"/><rect x="64" y="22" width="12" height="58"/><rect x="0" y="80" width="82" height="4"/><path d="M6 34 28 20 48 28 72 6" fill="none" stroke="var(--magenta)" stroke-width="4"/><circle cx="6" cy="34" r="5"/><circle cx="28" cy="20" r="5"/><circle cx="48" cy="28" r="5"/><circle cx="72" cy="6" r="5"/></svg>
    <div class="metric" style="left:85px;top:1382px"><div class="metric-num">251966</div><div class="metric-label">Games</div></div>
    <div class="metric" style="left:437px;top:1370px"><div class="metric-num">2692707</div><div class="metric-label">Games<br>Achievements</div></div>
    <div class="metric" style="left:798px;top:1382px"><div class="metric-num">339284</div><div class="metric-label">Game Stats</div></div>
    <div class="divider" style="left:425px;top:1278px;height:222px"></div>
    <div class="divider" style="left:797px;top:1274px;height:222px"></div>
    <svg class="abs" style="left:44px;top:1396px" width="20" height="30"><path d="M16 2 4 15l12 13" fill="none" stroke="#888" stroke-width="3"/></svg>
    <svg class="abs" style="left:1140px;top:1396px" width="20" height="30"><path d="M4 2l12 13L4 28" fill="none" stroke="#fff" stroke-width="3"/></svg>
  </section>

  <section class="users">
    <h2 class="abs center heading" style="top:1620px">Our Users</h2>
    <svg class="abs" style="left:0;top:1730px" width="1200" height="390">
      <defs>
        <linearGradient id="userFill" x1="0" y1="0" x2="0" y2="1"><stop offset="0" stop-color="#0d0318"/><stop offset="1" stop-color="#2b0838"/></linearGradient>
        <linearGradient id="userStroke" x1="0" y1="1" x2="1" y2="0">
          <stop offset="0" stop-color="#6a3cf5"/><stop offset="1" stop-color="#f01cf0"/>
        </linearGradient>
      </defs>
      <g fill="url(#userFill)" stroke="url(#userStroke)" stroke-width="2">
        <polygon points="114,9 350,9 386,140 386,377 148,377 114,250"/>
        <polygon points="471,9 707,9 743,140 743,377 505,377 471,250"/>
        <polygon points="828,9 1064,9 1100,140 1100,377 862,377 828,250"/>
      </g>
    </svg>
    <div class="user-card" style="left:113px">
      <div class="user-photo" role="img" aria-label="Portrait of a player with headphones in pink and blue light" style="background:linear-gradient(135deg,#e0407a,#6a6ad8 60%,#2a3a9a)"></div>
      <div class="user-name">LOREM IPSUM</div>
    </div>
    <div class="user-card" style="left:470px">
      <div class="user-photo" role="img" aria-label="Portrait of a smiling player wearing a gaming headset" style="background:linear-gradient(135deg,#2a2460,#4a5ab0 55%,#c04aa0)"></div>
      <div class="user-name">LOREM IPSUM</div>
    </div>
    <div class="user-card" style="left:827px">
      <div class="user-photo" role="img" aria-label="Portrait of a young player in violet light" style="background:linear-gradient(135deg,#5a3ad0,#2a1a60 55%,#b03ad0)"></div>
      <div class="user-name">LOREM IPSUM</div>
    </div>
    <svg class="abs" style="left:44px;top:1924px" width="20" height="30"><path d="M16 2 4 15l12 13" fill="none" stroke="#888" stroke-width="3"/></svg>
    <svg class="abs" style="left:1140px;top:1924px" width="20" height="30"><path d="M4 2l12 13L4 28" fill="none" stroke="#fff" stroke-width="3"/></svg>
  </section>

  <footer>
    <div class="brand abs" style="left:0;width:1200px;justify-content:center;top:2248px;gap:18px">
      <div class="brand-mark" style="width:40px;height:40px"></div>
      <div class="brand-name" style="font-size:36px">PlayTally<br>Collective</div>
    </div>
    <nav class="abs center footer-nav" style="top:2397px"><span>HOME</span><span>ABOUT US</span><span>VAPORN</span><span>GAME</span><span>CONTACT US</span></nav>
    <p class="abs center" style="top:2484px;font-size:16px;font-weight:600">COPYRIGHTS@2024.PLAYTALLY COLLECTIVE.ALL RIGHTS RESERVED</p>
  </footer>
</body>
</html>
```